New Business Card Design for Manufacturing

We are an engineering/manufacturing company that offers Advanced machining/assembly/engineering services, as well as innovative products for the heavy duty engine cooling markets.

We are looking to get a new business card designed that is clean and modern looking, but still fits the wide range of technical/skilled work we do.

- We hope to use this design as the base for other design work in new Presentations, web, and print work.

Industry/Entity Type

Engineering

Contact Information for Business Card

Our preferred color of blue is (RGB) 22/71/159 but can vary slightly from that color. Our content will be our Logo and full company name (Vantrell Forge Works, Inc.), company address, name, job title, phone number with extension, cell number, fax number, website, and email address on the cards.
We'd like the full company name next to the logo, but we are open to other interpretations of that layout.
Preferably, we would like the back side to be clean with just our logo, and the front to contain all of the contact information.

Colors
2f74b4
0355a3
85abd2

Requirements
Must have
• - Logo, company name, needed content - We are open to interpretation beyond that.
• - Standard size business card.
• - Horizontal orientation.
• - Enough space for lengthy names / job titles (for example, a job title could read "Directory of Human Resources" or "V.P. of Governmental Affairs"). We need this to look clean, whether the title be short (CEO) or long (as described above).

```html
<!DOCTYPE html>
<html lang="en">
<head>
<meta charset="utf-8">
<title>Vantrell Forge Works – Business Card</title>
<link rel="stylesheet" href="https://fonts.googleapis.com/css2?family=Roboto:wght@400;700;900&family=Roboto+Condensed:wght@700&display=swap">
<style>
  :root {
    --brand-blue: #0f4c9c;
    --card-white: #f4f4f4;
    --ink: #111111;
    --text-grey: #555555;
    --backdrop: #2b2b2b;
  }
  * { margin: 0; padding: 0; box-sizing: border-box; }
  html, body { width: 1200px; height: 960px; overflow: hidden; }
  body {
    background: var(--backdrop);
    font-family: "Roboto", Arial, sans-serif;
    position: relative;
  }
  .card {
    position: absolute;
    width: 600px;
    height: 343px;
    box-shadow: 0 3px 8px rgba(0,0,0,0.5);
  }
  .card--front { left: 314px; top: 113px; background: var(--card-white); }
  .card--back  { left: 311px; top: 472px; background: var(--brand-blue); }

  .brand {
    position: absolute;
    left: 52px;
    top: 58px;
    display: flex;
    align-items: center;
    gap: 10px;
  }
  .brand__mark {
    width: 14px; height: 14px;
    background: var(--brand-blue);
  }
  .brand__name {
    font-weight: 900;
    font-size: 19px;
    line-height: 1.1;
    color: var(--brand-blue);
    text-transform: uppercase;
  }
  .person {
    position: absolute;
    right: 46px;
    top: 62px;
    text-align: right;
  }
  .person__name {
    font-family: "Roboto Condensed", "Arial Narrow", sans-serif;
    font-weight: 700;
    font-size: 27px;
    line-height: 1;
    color: var(--brand-blue);
    text-transform: uppercase;
  }
  .person__title {
    font-size: 14px;
    color: var(--ink);
    margin-top: 4px;
  }
  .divider {
    position: absolute;
    left: 49px;
    right: 46px;
    top: 121px;
    height: 2px;
    background: var(--brand-blue);
  }
  .contacts {
    position: absolute;
    left: 52px;
    top: 179px;
    list-style: none;
    font-size: 14px;
    color: var(--text-grey);
    line-height: 19px;
  }
  .contacts li { display: flex; align-items: flex-start; gap: 11px; }
  .contacts li.contacts__address { margin-bottom: 7px; }
  .contacts svg { width: 14px; height: 14px; margin-top: 3px; flex: none; fill: var(--brand-blue); }

  .back-brand {
    position: absolute;
    left: 0; right: 0;
    top: 128px;
    text-align: center;
    color: #ffffff;
  }
  .back-brand__name {
    font-weight: 900;
    font-size: 40px;
    line-height: 1;
    text-transform: uppercase;
  }
  .back-brand__tagline {
    font-weight: 700;
    font-size: 17px;
    margin-top: 14px;
    text-transform: uppercase;
  }
</style>
</head>
<body>

<section class="card card--front" aria-label="Business card front">
  <div class="brand">
    <span class="brand__mark"></span>
    <span class="brand__name">Vantrell Forge<br>Works, Inc.</span>
  </div>
  <div class="person">
    <div class="person__name">Dorian Kessler</div>
    <div class="person__title">V.P. of Governmental Affairs</div>
  </div>
  <div class="divider"></div>
  <ul class="contacts">
    <li class="contacts__address">
      <svg viewBox="0 0 14 14"><path d="M7 0a5 5 0 0 0-5 5c0 3.6 5 9 5 9s5-5.4 5-9a5 5 0 0 0-5-5zm0 7a2 2 0 1 1 0-4 2 2 0 0 1 0 4z"/></svg>
      <span>4120 Larchmont Way<br>Fairbanks, Alaska 99712</span>
    </li>
    <li>
      <svg viewBox="0 0 14 14"><path d="M3 0.5l2.3 2.8-1.4 1.6c.8 1.9 2.3 3.4 4.2 4.2l1.6-1.4 2.8 2.3-1.2 2.4C6 12.2 1.8 8 1 2.2z"/></svg>
      <span>907 514 3862</span>
    </li>
    <li>
      <svg viewBox="0 0 14 14"><path d="M3.5 0h7a1 1 0 0 1 1 1v12a1 1 0 0 1-1 1h-7a1 1 0 0 1-1-1V1a1 1 0 0 1 1-1zm.8 1.5v9.5h5.4V1.5zM7 11.6a.8.8 0 1 0 0 1.6.8.8 0 0 0 0-1.6z"/></svg>
      <span>907 228 6147</span>
    </li>
    <li>
      <svg viewBox="0 0 14 14"><path d="M0 3h14v1L7 8 0 4zm0 2.2l7 4 7-4V12H0z"/></svg>
      <span>dorian@vantrellforgeworks.com</span>
    </li>
    <li>
      <svg viewBox="0 0 14 14"><circle cx="7" cy="7" r="7"/></svg>
      <span>www.vantrellforgeworks.com</span>
    </li>
  </ul>
</section>

<section class="card card--back" aria-label="Business card back">
  <div class="back-brand">
    <div class="back-brand__name">Vantrell Forge Works</div>
    <div class="back-brand__tagline">Shaping What Comes Next</div>
  </div>
</section>

</body>
</html>
```